Marine Services Letterhead design

We need a letterhead design for an Australian owned company in Victoria named K+T Harbour Works Pty Ltd. We provide linesmen and launches to assist the large ships that come into port.
Our colour is orange.
The final design should have a strong nautical theme and communicate safety and reliability.
I would like to use the letter head on invoices so it should print to pdf well.

Target Market(s)

Owners and representatives of shipping companies. It is not for general public

Industry/Entity Type

Nautical

Requirements
Must have
• A shipping theme, not overly complicated, featuring safety orange colours but not all orange of course.
The letterhead should just sit at the top of the page so I can use for invoices.
Nice to have
• Something elegant and stylish
Should not have
• cartoons or pop art

```html
<!DOCTYPE html>
<html lang="en">
<head>
<meta charset="utf-8">
<title>K+T Harbour Works Pty Ltd – Letterhead</title>
<link rel="stylesheet" href="https://fonts.googleapis.com/css2?family=PT+Sans:wght@400;700&display=swap">
<style>
  :root {
    --harbour-orange: #b0682a;
    --swoosh-black: #111111;
    --paper: #ffffff;
    --panel-grey: #f1f1f1;
    --ink: #3a3a3a;
    --header-text: #ffffff;
  }
  * { margin: 0; padding: 0; box-sizing: border-box; }
  html, body {
    width: 925px; height: 1200px; overflow: hidden;
    background: var(--paper);
    font-family: "PT Sans", Arial, sans-serif;
  }
  .letterhead {
    position: relative; width: 925px; height: 1200px;
    background: var(--paper); overflow: hidden;
  }
  .header-wave { position: absolute; top: 0; left: 0; width: 925px; height: 260px; }
  .header-contact {
    position: absolute; right: 41px; top: 48px;
    color: var(--header-text); font-size: 19px; text-align: right; line-height: 1;
  }
  .header-contact .phone { display: flex; align-items: center; justify-content: flex-end; gap: 5px; }
  .header-contact .abn { margin-top: 23px; }
  .brand-panel {
    position: absolute; left: 9px; top: 55px; width: 307px; height: 234px;
    background: var(--panel-grey);
  }
  .brand-square {
    position: absolute; left: 87px; top: 84px; width: 150px; height: 150px;
    background: var(--harbour-orange);
    box-shadow: 4px 6px 10px rgba(0,0,0,0.25);
  }
  .brand-name {
    position: absolute; left: 34px; top: 278px;
    color: var(--harbour-orange); font-weight: 700; font-size: 21px; white-space: nowrap;
  }
  .footer-address {
    position: absolute; left: 28px; top: 1148px;
    display: flex; align-items: center; gap: 7px;
    color: var(--ink); font-size: 21px;
  }
</style>
</head>
<body>
<main class="letterhead">
  <svg class="header-wave" viewBox="0 0 925 260" aria-hidden="true">
    <path fill="var(--harbour-orange)" d="M0,55 C40,30 110,22 185,23 C420,28 700,120 925,208 V0 H0 Z"/>
    <path fill="var(--swoosh-black)" d="M0,62 C40,36 110,28 185,28 C420,33 700,128 925,218 V242 C700,150 420,42 185,32 C110,31 40,44 0,68 Z"/>
  </svg>

  <div class="header-contact">
    <div class="phone">
      <svg width="17" height="17" viewBox="0 0 24 24" aria-hidden="true">
        <circle cx="12" cy="12" r="10.5" fill="none" stroke="#fff" stroke-width="1.6"/>
        <path fill="#fff" d="M9.2 6.5l1.6 2.6-1.1 1.2c.6 1.5 1.7 2.8 3.2 3.6l1.2-1 2.5 1.7-.9 2c-3.8.1-7.8-4.2-7.6-8.3z"/>
      </svg>
      <span>1300 555 018</span>
    </div>
    <div class="abn">ABN: 98765432101</div>
  </div>

  <div class="brand-panel"></div>
  <div class="brand-square"></div>
  <div class="brand-name">K+T Harbour Works Pty Ltd</div>

  <div class="footer-address">
    <svg width="14" height="22" viewBox="0 0 14 22" aria-hidden="true">
      <path fill="var(--harbour-orange)" d="M7 0C3.1 0 0 3.1 0 7c0 5 7 15 7 15s7-10 7-15c0-3.9-3.1-7-7-7zm0 9.6A2.6 2.6 0 1 1 7 4.4a2.6 2.6 0 0 1 0 5.2z"/>
    </svg>
    <span>PO Box 271 Seacliff 3930</span>
  </div>
</main>
</body>
</html>
```